Simple landing page for Brambles cookbook

I need a one page landingpage where customers can order the cookbook.
This is a cookbook of a collection of recipes from our deli that we used to run.
I need a landing page where customers can come and order the book. I also need it coded. I already have the domain through hostwell.
I can send the file of the book through wetransfer. It's too big to upload here. Just so you get the feel that I am looking for.
I attached a simple text as an introduction to the page. But I am open to any suggestions. I want it all to be about the experience that we are sharing the recipes with everybody and that it's for sale. The book is $29.99, shipping included.
Customers have to be able to click and buy the book from it.

Coding

Coded - Design and coding required

Number of Pages Required

1 page

Font styles to use
Sans Serif

Requirements
Must have
• Same colors as the cookbook

```html
<!DOCTYPE html>
<html lang="en">
<head>
<meta charset="utf-8">
<title>Brambles Sandwiches – Cookbook</title>
<link href="https://fonts.googleapis.com/css2?family=Roboto+Slab:wght@300;400;700;800&family=Zilla+Slab:wght@300;400;700&family=Figtree:wght@400;500&family=Poppins:wght@200&family=Dancing+Script:wght@400&display=swap" rel="stylesheet">
<style>
  :root{
    --ink:#0b0b0b;
    --crimson:#d8064a;
    --sand:#e9c29f;
    --white:#ffffff;
    --muted:#d8d8d8;
    --gold:#d9a06d;
    --grey:#8a8a8a;
    --slab:"Roboto Slab","Zilla Slab",serif;
  }
  *{margin:0;padding:0;box-sizing:border-box}
  html,body{width:1034px;height:1200px;overflow:hidden;background:var(--ink)}
  .page{position:relative;width:1034px;height:1200px;overflow:hidden;font-family:"Figtree",sans-serif;color:var(--white)}

  /* hero */
  .hero{position:absolute;left:0;top:0;width:1034px;height:420px;background:var(--ink)}
  .hero-backdrop{position:absolute;left:60px;top:60px;width:500px;height:360px;background:radial-gradient(ellipse at 45% 55%,#2a1c14 0%,#160e0a 40%,var(--ink) 75%)}
  .brand-block{position:absolute;left:140px;top:0;width:129px;height:56px;background:var(--white);color:var(--ink);font-family:var(--slab);font-weight:800;display:flex;flex-direction:column;align-items:center;justify-content:center;line-height:1}
  .brand-block .name{font-size:22px}
  .brand-block .sub{font-size:11.5px;margin-top:3px;letter-spacing:.3px}
  .hero-count{position:absolute;left:138px;top:76px;font-family:"Poppins",sans-serif;font-weight:200;font-size:80px;line-height:1;color:transparent;-webkit-text-stroke:1.6px var(--white)}
  .hero-title{position:absolute;left:140px;top:160px;font-family:var(--slab);font-weight:700;font-size:40px;line-height:50px;white-space:nowrap}
  .btn{position:absolute;display:block;background:var(--sand);color:var(--ink);font-family:var(--slab);font-weight:400;font-size:11px;text-decoration:none;height:36px;line-height:36px;width:121px;padding-left:33px}
  .btn::after{content:"";position:absolute;left:96px;top:18px;width:50px;height:1px;background:var(--white)}
  .btn-hero{left:141px;top:321px}
  .follow{position:absolute;left:757px;top:14px;display:flex;align-items:center;font-size:8.5px;font-weight:500;letter-spacing:3.2px}
  .follow .rule{width:40px;height:1px;background:var(--white);margin:0 6px 0 4px}
  .social-dot{display:inline-block;width:8px;height:8px;border-radius:50%;background:var(--white)}
  .book-visual{position:absolute;left:578px;top:36px;width:316px;height:374px;border-radius:4px;background:linear-gradient(135deg,#f3f8fb 0%,#d4e6f1 40%,#c58a55 72%,#e9eef2 100%)}
  .deco{position:absolute}

  /* stats */
  .stats{position:absolute;left:0;top:420px;width:1034px;height:121px;background:var(--crimson)}
  .stat{position:absolute;top:34px;display:flex;align-items:flex-start}
  .stat svg{margin-right:5px;margin-top:4px}
  .stat .num{font-family:var(--slab);font-weight:700;font-size:33px;line-height:1}
  .stat .label{font-size:15.5px;margin-top:2px}

  /* intro */
  .intro{position:absolute;left:0;top:541px;width:1034px;height:480px;background:radial-gradient(ellipse at 60% 40%,#1b1b1b 0%,var(--ink) 80%)}
  .burger-visual{position:absolute;left:95px;top:100px;width:342px;height:330px;border-radius:48% 48% 40% 40%;background:radial-gradient(ellipse at 50% 40%,#d98535 0%,#b55a1e 45%,#5f8a2e 78%,#1a1a1a 100%)}
  .eyebrow{position:absolute;left:459px;top:45px;font-size:9px;font-weight:500;letter-spacing:4.4px}
  .intro-title{position:absolute;left:459px;top:58px;font-family:var(--slab);font-weight:700;font-size:34px;line-height:48px;white-space:nowrap}
  .lead{position:absolute;left:462px;top:107px;width:420px;font-size:12.6px;font-weight:500;line-height:21px}
  .body-copy{position:absolute;left:460px;top:160px;width:432px;font-size:12.2px;line-height:22px;color:var(--muted)}
  .body-copy p+p{margin-top:4px}
  .signoff{position:absolute;left:459px;top:400px;width:430px;font-family:"Dancing Script",cursive;font-size:15.5px;line-height:22px;color:var(--gold)}

  /* purchase */
  .purchase{position:absolute;left:0;top:1021px;width:1034px;height:122px;background:var(--crimson)}
  .purchase-line{position:absolute;left:210px;top:36px;font-family:var(--slab);font-size:35px;line-height:48px;white-space:nowrap}
  .purchase-line .light{font-weight:300}
  .purchase-line .strong{font-weight:700}
  .purchase-line .price{font-weight:800;margin-left:16px}
  .btn-buy{left:733px;top:45px}

  /* footer */
  .footer{position:absolute;left:0;top:1143px;width:1034px;height:57px;background:var(--ink)}
  .footer-brand{position:absolute;left:140px;top:10px;font-family:var(--slab);font-weight:800;line-height:1}
  .footer-brand .name{font-size:21px;display:block}
  .footer-brand .sub{font-size:11.5px;display:block;margin-top:3px}
  .copyright{position:absolute;left:384px;top:21px;font-size:11px;color:var(--grey)}
  .copyright .accent{color:var(--crimson);font-family:var(--slab)}
  .footer .social-dot{position:absolute;left:884px;top:24px;width:9px;height:9px}
</style>
</head>
<body>
<div class="page">

  <header class="hero">
    <div class="hero-backdrop" role="img" aria-label="Dim photo of a sandwich on a dark table"></div>
    <div class="brand-block"><span class="name">Brambles</span><span class="sub">SANDWICHES</span></div>
    <div class="hero-count">28</div>
    <h1 class="hero-title">Delicous recipes<br>sandwiches,<br>sauces and burgers</h1>
    <a class="btn btn-hero" href="#buy">BUY NOW</a>
    <div class="follow">FOLLOW US<span class="rule"></span><span class="social-dot" role="img" aria-label="Friendbook"></span></div>
    <div class="book-visual" role="img" aria-label="Two copies of the Brambles Sandwiches cookbook with a sandwich on the cover"></div>
    <svg class="deco" style="left:456px;top:118px" width="10" height="10" aria-hidden="true"><path d="M5 0V10M0 5H10" stroke="#d9a06d" stroke-width="1.3"/></svg>
  </header>

  <section class="stats">
    <div class="stat" style="left:141px">
      <svg width="44" height="44" viewBox="0 0 44 44" fill="none" stroke="#fff" stroke-width="1.6" aria-hidden="true"><rect x="1" y="6" width="42" height="36" rx="2"/><path d="M1 14H43M8 2V10M16 2V10M28 2V10M36 2V10M7 20h30M7 26h30M7 32h30M7 38h22" stroke-dasharray="3 2"/></svg>
      <div><div class="num">12</div><div class="label">Year's journey</div></div>
    </div>
    <div class="stat" style="left:439px">
      <svg width="46" height="46" viewBox="0 0 46 46" fill="none" stroke="#fff" stroke-width="1.6" aria-hidden="true"><path d="M23 12C17 6 10 4 4 5V40C10 39 17 41 23 45C29 41 36 39 42 40V5C36 4 29 6 23 12ZM23 12V45M1 9V43H45V9"/></svg>
      <div><div class="num">05</div><div class="label">Cooking Chapters</div></div>
    </div>
    <div class="stat" style="left:714px">
      <svg width="42" height="48" viewBox="0 0 42 48" fill="none" stroke="#fff" stroke-width="1.6" aria-hidden="true"><path d="M1 14H41V47H1ZM12 20V9A9 9 0 0 1 30 9V20M14 22v6a7 7 0 0 0 14 0v-6"/></svg>
      <div><div class="num">1500</div><div class="label">Sales by customer</div></div>
    </div>
  </section>

  <section class="intro">
    <div class="burger-visual" role="img" aria-label="Photo of a crispy chicken burger with cheese and lettuce on a sesame bun"></div>
    <div class="eyebrow">INTRODUCTION</div>
    <h2 class="intro-title">Brambles Cookbook</h2>
    <p class="lead">Opening it's doors in January of 2010, Brambles European Deli was a sandwich shop in Alderton, New Brunswick, but also a lot more than</p>
    <div class="body-copy">
      <p>We spent five years with this business until it's eventual closure in April of 2015. It was a special time where we met tons of amazing people, who we loved to see and serve.</p>
      <p>Brambles started out as a deli but eventually morphed into the<br>sandwich shop we all know it as today.<br>We are overwhelmed with the continuous positive messages and comments we get on our Friendbook page that is still up and running.<br>Unfortunately, we can't open another Brambles, but we can offer you this collection of our recipes for you to try out at home with your family and<br>friends.</p>
    </div>
    <p class="signoff">If you do, please post your pictures of you making a meal or the finished product, or even enjoying it!</p>
    <svg class="deco" style="left:951px;top:34px" width="14" height="14" aria-hidden="true"><path d="M7 0V14M0 7H14" stroke="#d9a06d" stroke-width="1.6"/></svg>
    <svg class="deco" style="left:936px;top:309px" width="12" height="12" aria-hidden="true"><circle cx="6" cy="6" r="4" fill="none" stroke="#d9a06d" stroke-width="2"/></svg>
  </section>

  <section class="purchase" id="buy">
    <div class="purchase-line"><span class="light">Purchase </span><span class="strong">of your Book</span><span class="price">$29.99</span></div>
    <a class="btn btn-buy" href="#buy">BUY NOW</a>
  </section>

  <footer class="footer">
    <div class="footer-brand"><span class="name">Brambles</span><span class="sub">SANDWICHES</span></div>
    <p class="copyright">© 2022 <span class="accent">Brambles Sandwiches</span>. All right reserved</p>
    <span class="social-dot" role="img" aria-label="Friendbook"></span>
  </footer>

</div>
</body>
</html>
```